Bespoke Branding Agency "Tidal Crest" seeks uplifting wordpress site

Looking for a SIMPLE, CLEAN, easy to manage wordpress site for our start-up Branding business. Our company is "Tidal Crest" and the site should reflect our vision.

We formed the company after making the decision never to work the average 9 to 5 work life again. We have vowed to never work in traditional corporate culture again. We are committed to a happier life with reduced stress and increased job satisfaction.

We want to build brands that make people happy.

We want to work with people who believe that you don’t have to be an asshole to be successful.

We believe that success should not be measured in monetary terms, but rather in happiness scores.

We believe in the Corwin Ashdale song lyric "Rivers bend toward evening”.

We love sunflowers.

We prefer brevity over long wind.

We are motivated by creativity not money.

We love spending time with friends and family, and see this as our main priority in life.

We know life is short.

```html
<!DOCTYPE html>
<html lang="en">
<head>
<meta charset="utf-8">
<title>Tidal Crest — Services</title>
<link rel="stylesheet" href="https://fonts.googleapis.com/css2?family=Arimo:wght@400&family=PT+Sans:wght@400&display=swap">
<style>
  :root {
    --field: #7dc56a;
    --ink: #ffffff;
    --accent-rule: #2ab5c0;
    --placeholder: #a3d694;
  }
  * { margin: 0; padding: 0; box-sizing: border-box; }
  html, body { width: 1200px; height: 900px; overflow: hidden; }
  body {
    background: var(--field);
    color: var(--ink);
    font-family: "Arimo", Arial, sans-serif;
    position: relative;
  }
  .top-rule {
    position: absolute; left: 0; top: 0; width: 1200px; height: 3px;
    background: var(--accent-rule);
  }
  .top-notch { position: absolute; left: 532px; top: 0; }
  .section-title {
    position: absolute; left: 0; top: 112px; width: 1200px;
    text-align: center;
    font-family: "PT Sans", "Myriad Pro", sans-serif;
    font-weight: 400; font-size: 88px; line-height: 1; letter-spacing: 1px;
  }
  .section-intro {
    position: absolute; left: 50px; top: 245px; width: 1110px;
    font-size: 16px; line-height: 26px;
  }
  .service {
    position: absolute; top: 461px; width: 306px;
  }
  .service--logo { left: 50px; }
  .service--cards { left: 443px; }
  .service--apps { left: 844px; }
  .service__marker { display: block; }
  .service__badge {
    position: absolute; top: 61px; left: 43px;
    width: 222px; height: 222px;
  }
  .service__name {
    position: absolute; top: 320px; left: -20px; width: 346px;
    text-align: center; font-size: 34px; font-weight: 400; line-height: 1;
  }
  .service__text {
    position: absolute; top: 387px; left: 0; width: 300px;
    font-size: 13px; line-height: 16px;
  }
</style>
</head>
<body>
  <div class="top-rule"></div>
  <svg class="top-notch" width="132" height="62" viewBox="0 0 132 62" aria-hidden="true">
    <polygon points="0,2 132,2 66,61" fill="#ffffff"/>
  </svg>

  <h1 class="section-title">SERVICES</h1>

  <p class="section-intro">Contrary to popular belief, Lorem Ipsum is not simply random text. It has roots in a piece of classical Latin literature from 45 BC, making it over 2000 years old. Aldous Penhallow, a Latin professor at Marrow Ridge College in Virginia, looked up one of the more obscure Latin words, consectetur, from a Lorem Ipsum passage, and going through the cites of the word in classical literature, discovered the un-doubtable source. Lorem Ipsum comes from sections 1.10.32 and 1.10.33 of "de Finibus Bonorum et Malorum" (The Extremes of Good and Evil) by Tullus Averno, written in 45 BC. This book is a treatise on the theory of ethics, very popular during the Renaissance. The first line of Lorem Ipsum, "Lorem ipsum dolor sit amet..", comes from a line in section 1.10.32.</p>

  <section class="service service--logo">
    <svg class="service__marker" width="306" height="28" viewBox="0 0 306 28" aria-hidden="true">
      <rect x="0" y="0" width="306" height="4" fill="#ffffff"/>
      <polygon points="133,3 173,3 153,25" fill="#ffffff"/>
    </svg>
    <svg class="service__badge" viewBox="0 0 222 222">
      <circle cx="111" cy="111" r="108" fill="none" stroke="#ffffff" stroke-width="3"/>
      <circle cx="111" cy="111" r="78" fill="var(--placeholder)" role="img" aria-label="Illustration of round glasses above a moustache"/>
    </svg>
    <h2 class="service__name">LOGO</h2>
    <p class="service__text">It is a long established fact that a reader will be distracted by the readable content of a page when looking at its layout. The point of using Lorem Ipsum is that it has a more-or-less normal</p>
  </section>

  <section class="service service--cards">
    <svg class="service__marker" width="306" height="28" viewBox="0 0 306 28" aria-hidden="true">
      <rect x="0" y="0" width="306" height="4" fill="#ffffff"/>
      <polygon points="133,3 173,3 153,25" fill="#ffffff"/>
    </svg>
    <svg class="service__badge" viewBox="0 0 222 222">
      <circle cx="111" cy="111" r="108" fill="none" stroke="#ffffff" stroke-width="3"/>
      <rect x="26" y="71" width="170" height="80" rx="18" fill="var(--placeholder)" role="img" aria-label="Illustration of an ornate business card"/>
    </svg>
    <h2 class="service__name">BUSINESS CARDS</h2>
    <p class="service__text">It is a long established fact that a reader will be distracted by the readable content of a page when looking at its layout. The point of using Lorem Ipsum is that it has a more-or-less normal</p>
  </section>

  <section class="service service--apps">
    <svg class="service__marker" width="306" height="28" viewBox="0 0 306 28" aria-hidden="true">
      <rect x="0" y="0" width="306" height="4" fill="#ffffff"/>
      <polygon points="133,3 173,3 153,25" fill="#ffffff"/>
    </svg>
    <svg class="service__badge" viewBox="0 0 222 222" aria-hidden="true">
      <circle cx="111" cy="111" r="108" fill="none" stroke="#ffffff" stroke-width="3"/>
      <rect x="60" y="23" width="100" height="170" rx="40" fill="none" stroke="#ffffff" stroke-width="5"/>
      <rect x="73" y="46" width="74" height="120" rx="24" fill="none" stroke="#ffffff" stroke-width="4"/>
      <line x1="98" y1="34" x2="122" y2="34" stroke="#ffffff" stroke-width="3" stroke-linecap="round"/>
      <circle cx="110" cy="179" r="5" fill="none" stroke="#ffffff" stroke-width="2.5"/>
    </svg>
    <h2 class="service__name">MOBILE APPS</h2>
    <p class="service__text">It is a long established fact that a reader will be distracted by the readable content of a page when looking at its layout. The point of using Lorem Ipsum is that it has a more-or-less normal</p>
  </section>
</body>
</html>
```